Zielgruppe
Die Velorin Akademie bietet Kurse, Seminare & Coachings im Bereich der Kommunikation / Persönlichkeitsentwicklung an.
Folgendes Angebot besteht zur Zeit:
Seminare:
- 'Erste Schritte im Dialog', eine Einführung in die Kommunikation.
- 'Heitere Töchter, ruhige Väter' zum Thema Erziehung.
- 'Reifen mit Gelassenheit', zum Thema Älter werden und den Umgang damit.
Kurse:
- 'Gewaltfreie Kommunikation', Übungsgruppe
Coaching:
- Einzelsitzungen mit Hypnose
Ps: im Anhang unter 'Angabot_Vorlage.pdf' finden Sie mehr Infos zu den einezlenen Angebote.
Aufgabenstellung
Bitte berücksichtigen Sie, dass bereits ein Logo besteht (siehe Anhang).
Vom gesamteindruck her sollte die Website aufgeräumt, übersichtlich, harmonisch, freundlich & frisch wirken.
Es wäre super, wenn die Website authentisch wirkt (und weniger '0815 Business Website').
Bitte bedenken Sie, dass die Website sich an Private richtet, die sich nach einem 'strahlenderen & unbeschwerterem Lebene sehnen'.
Wir haben bereits viele Persönlichkeiten stärken können und möchten dies auch witerhin mit viel Herzblut machen.

```html
<!DOCTYPE html>
<html lang="de">
<head>
<meta charset="utf-8">
<title>Velorin Akademie</title>
<link rel="stylesheet" href="https://fonts.googleapis.com/css2?family=Raleway:ital,wght@0,400;0,500;0,600;0,700;1,400&display=swap">
<style>
:root{
  --canvas:#efe6df;
  --page:#ffffff;
  --panel:#f3f0eb;
  --apricot:#f0b985;
  --coral:#f26b43;
  --plum:#5b4b6c;
  --ink:#333333;
  --muted:#666;
  --taupe:#9b8776;
  --line:#9a9a9a;
}
*{box-sizing:border-box;margin:0;padding:0}
html,body{width:1200px;height:2999px;overflow:hidden;background:var(--canvas);font-family:'Raleway',sans-serif;color:var(--ink)}
.stage{position:relative;width:1200px;height:2999px;background:var(--canvas)}
.stage::before{content:"";position:absolute;left:0;top:0;width:73px;height:2999px;background:#fff}
.site{position:absolute;left:204px;top:55px;width:908px;height:2895px;background:var(--page)}
.abs{position:absolute}

/* header */
.topbar{left:0;top:0;width:908px;height:57px;background:rgba(255,255,255,.93);z-index:3}
.brand-small{left:26px;top:20px;font-size:11px;font-weight:600;letter-spacing:1.5px;color:#222}
.nav{right:46px;top:22px;display:flex;gap:30px;font-size:11.5px;font-weight:500;letter-spacing:.5px}
.nav a{color:#222;text-decoration:none}
.nav a.active{color:var(--coral);border:1.5px solid var(--coral);padding:3px 11px;margin-top:-5px}

/* hero */
.hero{left:0;top:57px;width:908px;height:467px;background:linear-gradient(180deg,#f1dcb8 0%,#e7b673 38%,#c98a45 62%,#8d5a2c 100%)}
.hero-glow{position:absolute;left:540px;top:40px;width:260px;height:260px;border-radius:50%;background:radial-gradient(circle,rgba(255,250,230,.95),rgba(255,230,170,0) 70%)}
.hero-title{left:0;top:270px;width:908px;text-align:center;color:#fff;font-size:38px;font-weight:500;letter-spacing:6px}
.hero-sub{left:0;top:326px;width:908px;text-align:center;color:#fff;font-size:18px;font-weight:500;letter-spacing:1px}
.hero-arrow{left:20px;top:190px}
.dots{left:432px;top:443px;display:flex;gap:6px}
.dots i{width:7px;height:7px;border-radius:50%;border:1px solid #fff}
.dots i:first-child{background:#fff}

/* newsletter */
.newsletter{left:0;top:539px;width:908px;height:59px;background:var(--apricot)}
.newsletter label{position:absolute;left:134px;top:24px;font-size:10.5px;font-weight:600;color:#fff}
.newsletter .field{position:absolute;left:397px;top:14px;width:319px;height:29px;background:#fff;border:1px solid #e7d8c8;font-size:10.5px;letter-spacing:1px;color:#888;padding:9px 11px}
.newsletter .ok{position:absolute;left:731px;top:19px;width:37px;height:20px;background:var(--coral);color:#fff;font-size:10.5px;font-weight:600;text-align:center;line-height:20px;letter-spacing:1px}

/* intro */
.h2{font-size:26px;font-weight:500;letter-spacing:1.3px;color:var(--plum);text-align:center}
.intro-title{left:0;top:649px;width:942px}
.intro-box{left:134px;top:697px;width:675px;height:192px;background:var(--panel);padding:26px 50px;font-size:13.5px;line-height:13px;color:#333}
.intro-box p+p{margin-top:13px}

/* offers band */
.offers-band{left:0;top:973px;width:908px;height:172px;background:linear-gradient(180deg,#faf4ea 0%,#fbe9cf 60%,#f3d9b6 100%)}
.lighthouse{left:0;top:973px;width:250px;height:172px;background:linear-gradient(180deg,#f6ecdf 0%,#e9d7c0 60%,#cdbba6 100%)}
.offers-title{left:0;top:1041px;width:968px}

/* cards */
.card{position:absolute;left:63px;width:780px;height:187px;background:var(--panel)}
.card .photo{position:absolute;left:71px;top:20px;width:155px;height:134px}
.card h3{position:absolute;left:264px;top:20px;font-size:13px;font-weight:700;color:var(--plum);letter-spacing:.3px}
.card .copy{position:absolute;left:264px;top:50px;width:484px;font-size:9.3px;line-height:12.5px;color:#555;text-align:justify}
.card .copy p+p{margin-top:12px}
.card .more{position:absolute;left:264px;top:156px;width:59px;height:20px;background:var(--coral);color:#fff;font-size:8px;font-weight:700;text-align:center;line-height:20px;letter-spacing:.8px}

/* landscape */
.vista{left:0;top:2235px;width:908px;height:249px;background:linear-gradient(180deg,#e9e5e2 0%,#d7cfc9 45%,#a49a92 70%,#4a3f3a 100%)}

/* footer contact */
.brand-foot{left:72px;top:2600px;width:240px;text-align:center;font-size:16px;font-weight:500;letter-spacing:2.5px;color:#222}
.address{left:72px;top:2660px;width:240px;text-align:center;font-size:13px;line-height:16px;color:#444}
.address strong{font-weight:600;letter-spacing:.6px;display:block;margin-bottom:14px;color:#333}
.address p{margin-bottom:14px}
.contact-head{left:473px;top:2512px;font-size:13.5px;line-height:16px;letter-spacing:.6px;color:#333}
.input{position:absolute;left:473px;width:319px;border:1.5px solid var(--line);font-size:10.5px;letter-spacing:1px;color:#777;padding:0 14px;line-height:28px}
.send{left:475px;top:2752px;width:165px;height:30px;background:var(--coral);color:#fff;font-size:11.5px;font-weight:600;text-align:center;line-height:30px;letter-spacing:1.5px}

/* bottom bar */
.legal{left:0;top:2819px;width:908px;height:76px;background:var(--taupe);color:#fff;font-size:13px;letter-spacing:.5px}
.legal span{position:absolute;top:30px}
</style>
</head>
<body>
<div class="stage">
  <div class="site">
    <header class="abs topbar">
      <div class="abs brand-small">VELORIN AKADEMIE</div>
      <nav class="abs nav">
        <a class="active" href="#">HOME</a>
        <a href="#">ANGEBOT</a>
        <a href="#">KONTAKT</a>
        <a href="#">ÜBER UNS</a>
      </nav>
    </header>

    <section class="abs hero" role="img" aria-label="Foto: Familie im goldenen Abendlicht auf einer Wiese, Kind auf den Schultern">
      <div class="hero-glow"></div>
      <svg class="abs hero-arrow" width="20" height="40" viewBox="0 0 20 40"><polyline points="18,2 3,20 18,38" fill="none" stroke="#fff" stroke-width="1.5"/></svg>
      <div class="abs hero-title">VELORIN AKADEMIE</div>
      <div class="abs hero-sub">NEUE PERSPECTIVEN • NEUE HORIZONTE</div>
      <div class="abs dots"><i></i><i></i><i></i></div>
    </section>

    <section class="abs newsletter">
      <label>ABONNIEREN SIE UNSEREN NEWSLETTER!</label>
      <div class="field">E-MAIL ADRESSE</div>
      <div class="ok">OK</div>
    </section>

    <h2 class="abs h2 intro-title">CHANCE AUF EIN NEUES LEVEL ZU KOMMEN</h2>
    <div class="abs intro-box">
      <p>Lorem ipsum dolor sit amet, mea cu nihil torquatos. Ad error civibus vivendum nec. Antiopam praesent sea an, id nam alii facete elaboraret.</p>
      <p>Urbanitas adolescens vituperatoribus vel in. Lorem voluptua posidonium eu sea, esse fabellas cu eam, cu vim tation nusquam. Nostrum iudicabit vix et, tota vivendo nominati has cu.</p>
      <p>Lorem ipsum dolor sit amet, mea cu nihil torquatos. Ad error civibus vivendum nec. Antiopam praesent sea an, id nam alii facete elaboraret. Urbanitas adolescens vituperatoribus vel in. Lorem voluptua posidonium eu sea, esse fabellas cu eam.</p>
    </div>

    <div class="abs offers-band"></div>
    <div class="abs lighthouse" role="img" aria-label="Foto: Leuchtturm mit rotem Dach vor hellem Himmel"></div>
    <h2 class="abs h2 offers-title">UNSERE AKTUELLE ANGEBOTE</h2>

    <article class="card" style="top:1177px">
      <div class="photo" role="img" aria-label="Foto: gestapelte Steine am Strand" style="background:linear-gradient(180deg,#e9e4de,#c9b29a 60%,#9c8676)"></div>
      <h3>SEMINAR: Erste Schritte im Dialog</h3>
      <div class="copy">
        <p>Jedes zusammenleben erfordert Kommunikation: ob in der Familie (auch mit Kindern), im Freundeskreis, oder im Arbeitsalltag. Verstehen und verstanden werden sind ausschlaggebend für Effektivität am Arbeitsplatz sowie Harmonie und erfüllende Beziehungen im persönlichen Leben.</p>
        <p>Sich selber besser zu verstehen eröffnet ungeahnte Möglichkeiten und Wahlfreiheit.</p>
      </div>
      <div class="more">MEHR</div>
    </article>

    <article class="card" style="top:1379px">
      <div class="photo" role="img" aria-label="Foto: Familie spaziert Hand in Hand über eine Brücke, schwarzweiss" style="background:linear-gradient(180deg,#d9d9d9,#9b9b9b 55%,#6e6e6e)"></div>
      <h3>SEMINAR: Heitere Töchter, ruhige Väter</h3>
      <div class="copy">
        <p><i>„Unter Erziehung versteht man die pädagogische Einflussnahme auf die Entwicklung und das Verhalten Heranwachsender“.</i> Erziehungstheorien gibt es unzählige, die das Spektrum von streng und autoritär bis hin zum Laisser-faire decken. Das selbst erlebte wird z.T. auch unreflektiert wiederholt und/oder wir verlieren uns in unzählige Ratgeber.</p>
        <p>Mithilfe der Neurowissenschaften wird uns klar, dass das oft kräftezerrende Ringen rund um die Erziehung absolut unnötig und überflüssig ist, ja sogar schädigend.</p>
      </div>
      <div class="more">MEHR</div>
    </article>

    <article class="card" style="top:1582px">
      <div class="photo" role="img" aria-label="Foto: Nahaufnahme einer Taschenuhr" style="background:linear-gradient(135deg,#5a6270,#b9bcc2 50%,#e6e4e0)"></div>
      <h3>SEMINAR: Zeit und Alternativen</h3>
      <div class="copy">
        <p>Zeit ist ein allgegenwärtiges (und manchmal leidiges) Thema, wie z.B „keine Zeit haben“ oder „die Zeit verfliegt im Nu“. Was IST jedoch Zeit? Wie und wo nehmen wir sie wahr? Welche Auswirkungen hat das „Zeit denken“? Was wäre, wenn wir der Zeit entkommen – aussteigen – könnten? Mit welchen Folgen? Welchen Zusammenhang haben Zeit und Alter?</p>
        <p><i>„Älter werden ist unumgänglich. Alt werden ist optional.“</i></p>
      </div>
      <div class="more">MEHR</div>
    </article>

    <article class="card" style="top:1786px">
      <div class="photo" role="img" aria-label="Foto: Gräser im Gegenlicht vor Bergen" style="background:linear-gradient(180deg,#cfd6dc,#d9c6a4 55%,#9c7a4e)"></div>
      <h3>SEMINAR: Gibt es Auswege aus DER Realität?</h3>
      <div class="copy">
        <p>Willkommen in der Realität!<br>Wir reden von DER Realität, der wir uns realistischer Weise beugen müssen. Was ist jedoch Realität? Wirk-lichkeit – etwas das „wirkt“? Tatsachen – wahrnehmbare Vorgänge? Wenn sie das ist, was wir wahrnehmen, ist sie subjektiv und liegt im Auge des Betrachters?<br>Wie bildet sich die Realität die wir erleben? Können wir Einfluss darauf nehmen?</p>
        <p>Könnten wir sie gar ändern?</p>
      </div>
      <div class="more">MEHR</div>
    </article>

    <article class="card" style="top:1992px">
      <div class="photo" role="img" aria-label="Foto: Wendeltreppe von oben gesehen" style="background:radial-gradient(circle at 55% 60%,#3a3a3a,#8a8a8a 40%,#d6d3cf 80%)"></div>
      <h3>EINZELSITZUNGEN: Coaching mit Hypnose</h3>
      <div class="copy">
        <p>Einzelsitzungen…</p>
        <p>Hast du Lust, die Kraft deines Unterbewusstseins zu erfahren?<br>Hypnose macht es erlebbar und ermöglicht, Veränderungsarbeit (wie z.B. Verhalten, Rauchen, Phobien…) erfolgreich umzusetzen</p>
      </div>
      <div class="more">MEHR</div>
    </article>

    <div class="abs vista" role="img" aria-label="Foto: Person sitzt auf einem Felsen über einem dunstigen Bergtal"></div>

    <div class="abs brand-foot">VELORIN AKADEMIE</div>
    <div class="abs address">
      <strong>VELORIN AKADEMIE GMBH.</strong>
      <p>Lindenweg 9<br>4321 Sonnental</p>
      <p>TEL: 0176 987 210<br>info@velorinakademie.ch</p>
    </div>

    <div class="abs contact-head">NOCH FRAGEN, ANREGUNGEN?<br>SCHREIBEN SIE UNS!</div>
    <div class="input" style="top:2556px;height:31px">NAME</div>
    <div class="input" style="top:2599px;height:31px">E-MAIL ADRESSE</div>
    <div class="input" style="top:2639px;height:99px">NACHRICHT</div>
    <div class="abs send">SENDEN</div>

    <footer class="abs legal">
      <span style="left:55px">Datenschutz</span>
      <span style="left:171px">Impressum</span>
      <span style="left:385px">VELORIN AKADEMIE | 2019</span>
    </footer>
  </div>
</div>
</body>
</html>
```